Zielgruppe
Immobilienmakler
Aufgabenstellung
Top moderne hochwertige Visitenkate, wir hätten gerne eine sehr hochwertig moderne Visitenkarte mit Bild vom Mitarbeiter... Anbei habe ich die alte Visitenkarte die ich sehr kindlich finde... Es sollte jetzt sehr exklusive aussehen. Alle Daten können von der alten Visitenkarte übernommen werden.. danke

```html
<!DOCTYPE html>
<html lang="de">
<head>
<meta charset="utf-8">
<title>Velta Agentur – Visitenkarte</title>
<link href="https://fonts.googleapis.com/css2?family=Inter:wght@300;400;700&display=swap" rel="stylesheet">
<style>
  :root {
    --backdrop: #2b2b2a;
    --green-top: #021a0c;
    --green-bottom: #06361a;
    --paper: #ffffff;
    --ink: #1a1a1a;
    --ink-soft: #333333;
    --photo-light: #e6e6e6;
    --photo-dark: #8a8a8a;
  }
  html, body {
    margin: 0;
    padding: 0;
    width: 935px;
    height: 1200px;
    overflow: hidden;
    background: var(--backdrop);
    font-family: "Inter", Arial, sans-serif;
  }
  .canvas {
    position: relative;
    width: 935px;
    height: 1200px;
  }
  .card {
    position: absolute;
    width: 540px;
    height: 350px;
    box-shadow: 0 12px 28px rgba(0, 0, 0, 0.35);
    overflow: hidden;
  }
  .card-front {
    left: 208px;
    top: 198px;
    background: linear-gradient(180deg, var(--green-top) 0%, var(--green-bottom) 100%);
    display: flex;
    align-items: center;
    justify-content: center;
  }
  .brand-name {
    color: var(--paper);
    font-weight: 700;
    font-size: 31px;
    letter-spacing: -0.5px;
    margin-top: -10px;
  }
  .card-back {
    left: 214px;
    top: 670px;
    background: var(--paper);
  }
  .portrait {
    position: absolute;
    left: 0;
    top: 11px;
    width: 198px;
    height: 339px;
    background: linear-gradient(160deg, var(--photo-light) 0%, var(--photo-dark) 100%);
  }
  .contact {
    position: absolute;
    left: 291px;
    top: 118px;
    color: var(--ink-soft);
    font-weight: 300;
    font-size: 14.5px;
    line-height: 19px;
  }
  .contact p { margin: 0; }
  .person-name {
    font-weight: 700;
    font-size: 17.5px;
    color: var(--ink);
    margin: 0 0 6px;
  }
  .role { margin-bottom: 18px !important; }
  .address { margin-bottom: 8px !important; }
  .phones { margin-bottom: 5px !important; }
  .email { margin-bottom: 4px !important; }
</style>
</head>
<body>
  <div class="canvas">
    <section class="card card-front">
      <div class="brand-name">Velta Agentur</div>
    </section>

    <section class="card card-back">
      <div class="portrait" role="img" aria-label="Schwarz-Weiß-Porträt des Mitarbeiters mit Sakko über der Schulter"></div>
      <div class="contact">
        <h1 class="person-name">Tobias Keller</h1>
        <p class="role">Dipl. Immobilienmanager<br>Geschäftsführer</p>
        <p class="address">Am Anger 12 | 6850 Dornbirn</p>
        <p class="phones">+43 5572 41 872 20<br>+43 660 4827 195</p>
        <p class="email">tobias@velta-agentur.com</p>
        <p class="web">www.velta-agentur.com</p>
      </div>
    </section>
  </div>
</body>
</html>
```